Regenerative Wellness Flyer to recruit Dr offices and clinics

This is a flyer that will be used to recruit new Dr offices and clinics to make them aware of a brand new product that is about to hit the market.

I uploaded an older flyer that I do like. This product is not Stem Cells but fixes a lot of the same things. So the title could be Regenerative Wellness and Cell Factor Therapy.

I also loaded a multiple page info on the product.

I would like to be able to change out logo's & contact information as I have a couple sales people helping push this. I also attached my logo, Veradune. Would like to be able to a QR code...

This is the landing page that the flyer will drive Dr's to:
https://app.plinorvast.com/v2/preview/K3QwzRtaLmNpUe8sJdVb?notrack=true

Target Market(s)

Dr's office, clinics, alternative wellness clinics

Industry/Entity Type

health & wellness

Colors
0054AA
0677BA
7BADD7
CADEEF
E8F1F8
00AB8E
00BBA5
67D7C9
C6EFE9
E9F9F6

Requirements
Nice to have
• The ability to change out the logo/contact info areas

```html
<!DOCTYPE html>
<html lang="en">
<head>
<meta charset="utf-8">
<title>Veradune Wellness – Regenerative Therapy Flyer</title>
<link href="https://fonts.googleapis.com/css2?family=Oswald:wght@700&family=Barlow+Condensed:wght@500;600&family=Montserrat:wght@500;600;700&display=swap" rel="stylesheet">
<style>
  :root {
    --navy: #0054AA;
    --blue: #0677BA;
    --sky: #7BADD7;
    --ice: #CADEEF;
    --mist: #E8F1F8;
    --teal: #00AB8E;
    --aqua: #00BBA5;
    --mint: #67D7C9;
    --foam: #C6EFE9;
    --frost: #E9F9F6;
    --ink: #1d1f24;
    --white: #ffffff;
  }
  * { box-sizing: border-box; margin: 0; padding: 0; }
  html, body { width: 800px; height: 1200px; overflow: hidden; background: var(--white); }
  .flyer { position: relative; width: 800px; height: 1200px; background: var(--white); font-family: "Montserrat", sans-serif; color: var(--ink); overflow: hidden; }

  .headline { position: absolute; left: 58px; top: 56px; width: 420px; }
  .headline__kicker { font-family: "Oswald", sans-serif; font-weight: 700; color: var(--teal); font-size: 52px; line-height: 54px; letter-spacing: -0.5px; }
  .headline__title { font-family: "Barlow Condensed", sans-serif; font-weight: 500; color: var(--navy); font-size: 42px; line-height: 50px; margin-top: 12px; }
  .headline__intro { font-size: 13.2px; font-weight: 600; line-height: 17px; margin-top: 6px; width: 400px; }

  .brand { position: absolute; left: 465px; top: 30px; width: 280px; text-align: center; }
  .brand__disc { width: 250px; height: 250px; border-radius: 50%; background: var(--foam); margin: 0 auto; }
  .brand__name { font-family: "Montserrat", sans-serif; font-weight: 700; font-size: 25px; line-height: 30px; color: var(--teal); margin-top: 16px; white-space: nowrap; }
  .brand__tagline { font-size: 12.5px; letter-spacing: 3px; color: var(--teal); margin-top: 8px; font-weight: 500; white-space: nowrap; }

  .features { position: absolute; left: 0; top: 384px; width: 800px; height: 204px; background: var(--mist); }
  .feature { position: absolute; top: 30px; width: 180px; text-align: center; }
  .feature__icon { width: 84px; height: 84px; margin: 0 auto; display: block; }
  .feature__label { font-family: "Barlow Condensed", sans-serif; font-weight: 500; font-size: 19px; line-height: 23px; margin-top: 22px; color: var(--ink); }

  .details { position: absolute; left: 0; top: 588px; width: 800px; height: 190px; }
  .spec { position: absolute; top: 40px; }
  .spec__title { font-family: "Barlow Condensed", sans-serif; font-weight: 600; font-size: 20px; color: var(--navy); line-height: 20px; }
  .spec__sub { font-size: 13px; color: var(--navy); margin-top: 2px; }
  .spec__list { list-style: none; margin-top: 6px; }
  .spec__list li { position: relative; padding-left: 18px; font-size: 13px; line-height: 16.5px; margin-bottom: 6px; font-weight: 500; white-space: nowrap; }
  .spec__list svg { position: absolute; left: 0; top: 3px; width: 11px; height: 11px; }
  .vial { position: absolute; left: 240px; top: 30px; width: 92px; height: 130px; border-radius: 14px 14px 18px 18px; background: linear-gradient(180deg, var(--sky) 0%, var(--sky) 18%, var(--mist) 22%, #f4f6f7 70%, #c9ced3 100%); }

  .science { position: absolute; left: 0; top: 778px; width: 800px; height: 254px; background: var(--blue); color: var(--white); }
  .science__title { position: absolute; left: 58px; top: 18px; font-family: "Barlow Condensed", sans-serif; font-weight: 600; font-size: 20px; color: var(--white); }
  .science__quote { position: absolute; left: 58px; top: 52px; width: 470px; font-size: 13.4px; line-height: 17px; font-weight: 500; color: var(--white); }
  .science__body { position: absolute; left: 58px; top: 104px; width: 466px; font-size: 11.2px; line-height: 14.2px; text-align: justify; color: var(--white); }

  .anatomy { position: absolute; left: 535px; top: 624px; width: 244px; height: 442px; border-radius: 50%; background: radial-gradient(ellipse at 50% 45%, var(--frost) 0%, var(--ice) 75%, var(--sky) 100%); }

  .cta { position: absolute; left: 58px; top: 1068px; width: 700px; }
  .cta__title { font-family: "Barlow Condensed", sans-serif; font-weight: 600; font-size: 20px; color: var(--navy); white-space: nowrap; }
  .cta__sub { font-size: 12.4px; font-weight: 500; margin-top: 2px; white-space: nowrap; }
  .cta__button { position: absolute; left: 528px; top: 2px; width: 146px; height: 28px; border-radius: 8px; background: var(--teal); color: var(--white); font-family: "Barlow Condensed", sans-serif; font-weight: 600; font-size: 18px; line-height: 24px; text-align: center; border: 2px solid var(--foam); box-shadow: 0 0 0 1px var(--teal); }

  .contact { position: absolute; left: 50px; right: 40px; top: 1138px; display: flex; justify-content: space-between; align-items: center; }
  .contact__item { display: flex; align-items: center; gap: 6px; font-size: 19px; font-weight: 500; white-space: nowrap; }
  .contact__item svg { width: 19px; height: 19px; flex: none; }
  .footer-rule { position: absolute; left: 0; bottom: 0; width: 800px; height: 5px; background: var(--blue); }
</style>
</head>
<body>
<main class="flyer">

  <header class="headline">
    <div class="headline__kicker">NEW<br>REVOLUTIONARY</div>
    <h1 class="headline__title">Medical Evidence Based<br>Regenerative Therapy</h1>
    <p class="headline__intro">We developed a way to process, collect, measure, and apply all the regenerative messages we’re born with mimicking the body’s complete natural homeostasis and response to stressors in our youth.</p>
  </header>

  <div class="brand">
    <div class="brand__disc"></div>
    <div class="brand__name">Veradune Wellness</div>
    <div class="brand__tagline">BODY MIND AND SPIRIT</div>
  </div>

  <section class="features">
    <div class="feature" style="left:27px">
      <svg class="feature__icon" viewBox="0 0 84 84"><use href="#icon-lab"/></svg>
      <p class="feature__label">ALL Indications in<br>ONE product</p>
    </div>
    <div class="feature" style="left:210px">
      <svg class="feature__icon" viewBox="0 0 84 84"><use href="#icon-lab"/></svg>
      <p class="feature__label">Regulatory Freedom</p>
    </div>
    <div class="feature" style="left:391px">
      <svg class="feature__icon" viewBox="0 0 84 84"><use href="#icon-lab"/></svg>
      <p class="feature__label">cGMP &amp; FDA Registered<br>Laboratory</p>
    </div>
    <div class="feature" style="left:574px">
      <svg class="feature__icon" viewBox="0 0 84 84"><use href="#icon-lab"/></svg>
      <p class="feature__label">Shelf Stable: NO Dry Ice,<br>NO Feezers</p>
    </div>
  </section>

  <section class="details">
    <div class="spec" style="left:58px">
      <h2 class="spec__title">PHYSICAL FORM</h2>
      <ul class="spec__list">
        <li><svg viewBox="0 0 12 12"><use href="#icon-tick"/></svg>NO DRY ICE<br>(no live cells or DNA)</li>
        <li><svg viewBox="0 0 12 12"><use href="#icon-tick"/></svg>NO FREEZERS</li>
        <li><svg viewBox="0 0 12 12"><use href="#icon-tick"/></svg>SHELF STABLE<br>-3yr expiration date</li>
      </ul>
    </div>
    <div class="vial" role="img" aria-label="Product photo: small glass vial of white powder with a blue cap"></div>
    <div class="spec" style="left:352px">
      <h2 class="spec__title">APPLICATIONS</h2>
      <p class="spec__sub">(ALL LEGAL)</p>
      <ul class="spec__list">
        <li><svg viewBox="0 0 12 12"><use href="#icon-tick"/></svg>IV, IN, IM, NB, IT,<br>IA, SQ, IP, MC.IV</li>
        <li><svg viewBox="0 0 12 12"><use href="#icon-tick"/></svg>Intrathecal</li>
        <li><svg viewBox="0 0 12 12"><use href="#icon-tick"/></svg>Eye Drops, Hair, Facial</li>
      </ul>
    </div>
  </section>

  <section class="science">
    <h2 class="science__title">COMPLETE REGENERATIVE THERAPY</h2>
    <p class="science__quote">“True, complete regenerative therapies are NOT STEM CELLS, EXOSOMES, PRP, BM OR ANY TYPICAL BIOLOGICAL DERIVATION.”</p>
    <p class="science__body">A Sophisticated cGMP &amp; FDA Registered laboratory subjects the stem cells to normal biological stressors, causing them to naturally express ALL 30,000+ gene expressions (protein, m/mi/lnc RNA) in the human genome: ALL cytokines, ALL growth factors, etc. These Regenerative Messages are kept in their NATURAL RATIOS of those at birth, nothing synthesized Importantly, these regenerative messages are then isolated, verified, and measured, ensuring that what is collected has no residual DNA or idiosyncratic biomarkers. This advancement in science results in a synthesis of naturally regenerative material that can be safely applied to practically anyone.</p>
  </section>

  <div class="anatomy" role="img" aria-label="Illustration of a standing human anatomy figure surrounded by small organ images: brain, eye, heart, lungs, joints, liver and more"></div>

  <section class="cta">
    <h2 class="cta__title">CONCERNED ABOUT FDA STRONGHOLD IN REGENERATIVE MEDICINE?</h2>
    <p class="cta__sub">A powerful &amp; safe new to market approach: FREE from regulatory constraints</p>
    <a class="cta__button">GET A FREE GUIDE</a>
  </section>

  <footer class="contact">
    <span class="contact__item"><svg viewBox="0 0 20 20"><circle cx="10" cy="10" r="10" fill="var(--teal)"/><path d="M6.2 5.2l2 0 1 2.6-1.3 1a6 6 0 0 0 3.3 3.3l1-1.3 2.6 1v2a1.2 1.2 0 0 1-1.3 1.2A9 9 0 0 1 5 6.5a1.2 1.2 0 0 1 1.2-1.3z" fill="#fff"/></svg>(512) 555-0187</span>
    <span class="contact__item"><svg viewBox="0 0 20 20"><circle cx="10" cy="10" r="10" fill="var(--teal)"/><rect x="5" y="6.5" width="10" height="7" rx="1" fill="none" stroke="#fff" stroke-width="1.3"/><path d="M5.3 7l4.7 3.6L14.7 7" fill="none" stroke="#fff" stroke-width="1.3"/></svg>mara@VeraduneFARM.com</span>
    <span class="contact__item"><svg viewBox="0 0 20 20"><circle cx="10" cy="10" r="10" fill="var(--teal)"/><g fill="none" stroke="#fff" stroke-width="1.1"><circle cx="10" cy="10" r="5.5"/><ellipse cx="10" cy="10" rx="2.4" ry="5.5"/><path d="M4.5 10h11M5.3 7.2h9.4M5.3 12.8h9.4"/></g></svg>veradunefarm.com</span>
  </footer>

  <div class="footer-rule"></div>

  <svg width="0" height="0" style="position:absolute" aria-hidden="true">
    <defs>
      <g id="icon-lab">
        <circle cx="42" cy="42" r="42" fill="#0054AA"/>
        <g fill="none" stroke="#fff" stroke-width="2.2" stroke-linecap="round" stroke-linejoin="round">
          <path d="M22 22v8M18 26h8M19.2 23.2l5.6 5.6M24.8 23.2l-5.6 5.6"/>
          <path d="M28 36a3 3 0 0 1 6 0v18a5 5 0 1 1-6 0z"/>
          <path d="M31 44v12"/>
          <path d="M40 22h14v6h-14zM42 28v4l-3 3v26h16V35l-3-3v-4"/>
          <path d="M39 42h16M39 52h16"/>
        </g>
      </g>
      <g id="icon-tick">
        <circle cx="6" cy="6" r="5.2" fill="none" stroke="#00AB8E" stroke-width="1.4"/>
        <path d="M3.5 6.2l1.8 1.8 3.3-3.4" fill="none" stroke="#00AB8E" stroke-width="1.5" stroke-linecap="round" stroke-linejoin="round"/>
      </g>
    </defs>
  </svg>
</main>
</body>
</html>
```